πΈ Full Website Redesign on Wix β The Willowmere Atelier (Feminine, Sophisticated, Nature-Inspired)
Business Name: The Willowmere Atelier
Current Site: https://quorvalen.example/Tz8pLmQ (for structure reference only)
Platform: Wix
Business Type: Women-led Canadian online retail business
Location: Canada
π About The Willowmere Atelier
The Willowmere Atelier is a boutique e-commerce store specializing in roses and blooming plants, created for modern plant lovers who appreciate beauty, quality, and storytelling.
We are a small, women-led business in Ontario, Canada, and our audience is primarily women who are drawn to floral aesthetics, a calming user experience, and elevated design.
Our name β The Willowmere Atelier β represents both a curated collection of blooms and a love of thoughtful, meaningful beauty.
π» Project Overview
We are looking for a full website redesign from scratch (built on Wix) that reflects our brand identity: feminine, sophisticated, romantic, and grounded in nature.
The current version of the site was just a test layout β we now want a fresh, cohesive design vision that speaks directly to our female Canadian customer base with a clean, modern, and elegant interface.
This project is not just about functionality β itβs about crafting an experience that feels like a digital floral sanctuary.
π― What We Need
Full website design and development in Wix (you can start fresh)
Custom homepage design with storytelling and a welcoming brand vibe
Pages to include (subject to refinement):
Home
Shop (products will be added by us later)
About
Contact
FAQ / Info
Blog or Guides (optional placeholder)
Sophisticated visual branding:
Muted rose, blush, and earthy tones
Clean, modern layout with elegant typography
Feminine, natural, soft design elements (think floral details, soft lines, minimalism with warmth)
Optimized for both desktop and mobile
Set up global styles (font, color palette, button styles, etc.)
Guidance or setup for product sections using Wixβs eCommerce system
Create beautiful reusable sections (for us to duplicate later as needed)
π· Brand Style
We are aiming for a website that feels like:
A curated botanical boutique
Feminine and warm β but not overly girly
Sophisticated and soft, never cluttered
Clean but not sterile
Relaxed elegance with a focus on natural beauty
Color palette:
Muted rose
Warm blush tones
Cream, soft beige, earthy sage
Very subtle contrast β no stark black-and-white
Typography:
Elegant serif or soft sans-serif pairings
Easy to read but with character
π Technical Info
Platform: Wix
No custom coding required (Wix-native tools preferred)
We will handle product uploads
Weβll provide any imagery you request
π¦ Deliverables
Fully designed Wix website (ready to publish)
All pages complete with consistent design and layout
Mobile-responsive layout
Design system set up for future content (colors, typography, etc.)
Optional: Style guide PDF for brand reference (bonus)
π Timeline
Weβd like the website to be completed within 1-2 weeks after project start. Please let us know your availability.
β
To Apply
Please include:
Portfolio (especially if youβve done Wix, floral, feminine, or nature-inspired work)
A short message on how you'd approach this project
Timeline/availability
We're looking for someone who understands how to design for emotion, beauty, and ease β not just functionality. If you love soft colors, delicate details, and creating meaningful digital experiences for women, we'd love to hear from you.
πΈ Letβs build something beautiful together!
Rose enthusiasts

```html
<!DOCTYPE html>
<html lang="en">
<head>
<meta charset="utf-8">
<title>The Willowmere Atelier</title>
<link rel="stylesheet" href="https://fonts.googleapis.com/css2?family=Poppins:wght@500;600;700;800&family=Figtree:wght@400;500;600&display=swap">
<style>
:root{
  --mauve:#8a6b7e;
  --blush:#d9a3af;
  --rose:#f2b3c2;
  --rose-btn:#e7a7b6;
  --plum-btn:#7d6171;
  --cream:#fff7f4;
  --white:#ffffff;
  --line:rgba(255,255,255,.75);
}
*{box-sizing:border-box;margin:0;padding:0}
html,body{width:1200px;height:3548px;overflow:hidden}
body{position:relative;background:var(--mauve);font-family:"Figtree",sans-serif;color:var(--white)}
.abs{position:absolute}
.photo{position:absolute;border-radius:12px}
.heading{font-family:"Poppins",sans-serif;font-weight:800;color:var(--white);letter-spacing:-.5px}
.divider-ornament{position:absolute;width:92px;height:10px;border-radius:5px;background:linear-gradient(90deg,transparent,rgba(255,255,255,.7),transparent)}
.floral-art{position:absolute;background:radial-gradient(ellipse at center,rgba(242,179,194,.35),transparent 70%)}

/* hero */
.hero{position:absolute;left:0;top:0;width:1200px;height:661px;background:linear-gradient(180deg,#cbb9ad 0%,#e7d3c9 35%,#bfa89f 70%,#9d8a84 100%)}
.hero-photo{position:absolute;inset:0;background:
  radial-gradient(ellipse 220px 140px at 140px 180px,rgba(255,250,240,.9),transparent),
  radial-gradient(ellipse 180px 120px at 120px 260px,rgba(190,30,70,.55),transparent),
  radial-gradient(ellipse 260px 160px at 700px 200px,rgba(245,170,130,.75),transparent),
  radial-gradient(ellipse 200px 150px at 1080px 160px,rgba(255,250,240,.9),transparent),
  radial-gradient(ellipse 600px 200px at 600px 560px,rgba(120,140,110,.35),transparent)}
.hero-shade{position:absolute;inset:0;background:rgba(60,40,50,.12)}
.logo{position:absolute;display:flex;align-items:center;gap:10px;font-family:"Poppins",sans-serif;font-weight:700;color:var(--white)}
.logo .dot{width:14px;height:14px;border-radius:50%;background:var(--white)}
.nav{position:absolute;left:507px;top:36px;display:flex;align-items:center;font-family:"Poppins",sans-serif;font-weight:600;font-size:15px}
.nav a{color:var(--white);text-decoration:none;padding:7px 16px;border-radius:16px;margin-right:6px}
.nav a.active{background:var(--rose-btn)}
.hero-title{position:absolute;left:0;width:1200px;text-align:center;font-family:"Poppins",sans-serif;font-weight:800;letter-spacing:-1px}
.btn{position:absolute;display:flex;align-items:center;justify-content:center;border-radius:30px;font-family:"Poppins",sans-serif;font-weight:700;text-transform:uppercase;color:var(--white)}
.btn-rose{background:var(--rose-btn)}
.btn-plum{background:var(--plum-btn)}

/* about */
.about-frame{position:absolute;left:160px;top:738px;width:470px;height:494px;border:1px solid var(--line)}
.about-text{position:absolute;left:682px;top:895px;width:370px;font-size:16.5px;line-height:24px}
.about-text p+p{margin-top:24px}

/* flowers */
.flowers{position:absolute;left:0;top:1292px;width:1200px;height:629px;background:var(--blush)}
.product-card{position:absolute;top:205px;width:210px;height:358px;border:1px solid var(--line);border-radius:12px;text-align:center}
.product-card .photo{left:0;top:0;width:208px;height:227px;border-radius:11px 11px 0 0}
.product-name{position:absolute;top:245px;width:100%;font-family:"Poppins",sans-serif;font-weight:700;font-size:13.5px}
.product-price{position:absolute;top:270px;width:100%;font-family:"Poppins",sans-serif;font-size:13px;font-weight:500}
.product-card .btn{left:54px;top:305px;width:100px;height:26px;font-size:11px}

/* occasion */
.occasion-label{position:absolute;top:2450px;width:287px;text-align:center;font-family:"Poppins",sans-serif;font-weight:700;font-size:17px}
.occasion-label::after{content:"";display:block;width:38px;height:2px;background:var(--white);margin:18px auto 0}

/* blog */
.blog{position:absolute;left:0;top:2542px;width:1200px;height:690px;background:var(--blush)}
.blog-card{position:absolute;top:194px;width:267px}
.blog-card .photo{position:relative;display:block;width:267px;height:188px;border-radius:14px}
.blog-title{margin:22px 4px 0;font-family:"Poppins",sans-serif;font-weight:700;font-size:17px;line-height:22px;color:var(--plum-btn)}
.blog-excerpt{margin:12px 4px 0;font-size:13px;line-height:18px;color:#f9eef1}
.blog-card .btn{position:relative;margin:18px 4px 0;width:96px;height:28px;font-size:9px}

/* footer */
.footer-col h4{font-family:"Poppins",sans-serif;font-weight:600;font-size:16px;margin-bottom:10px}
.footer-col li{list-style:none;font-size:12px;line-height:18px}
.contact-row{display:flex;align-items:center;gap:12px;font-size:12px;margin-bottom:14px}
.social{display:flex;gap:9px}
.social span{width:32px;height:32px;border:2px solid var(--white);border-radius:50%}
</style>
</head>
<body>

<!-- Hero -->
<section class="hero">
  <div class="hero-photo" role="img" aria-label="Vases of cream, pink, peach and red roses on a shop counter"></div>
  <div class="hero-shade"></div>
  <div class="logo" style="left:152px;top:34px;font-size:25px"><span class="dot"></span>The Willowmere Atelier</div>
  <nav class="nav">
    <a class="active" href="#">Home</a><a href="#">About</a><a href="#">Shop</a><a href="#">FAQ</a><a href="#">Blog</a><a href="#">Contact</a>
  </nav>
  <svg class="abs" style="left:986px;top:40px" width="22" height="22" viewBox="0 0 22 22" aria-label="Account"><circle cx="11" cy="6" r="5" fill="#fff"/><path d="M1 22c0-6 4-9 10-9s10 3 10 9z" fill="#fff"/></svg>
  <svg class="abs" style="left:1028px;top:40px" width="28" height="24" viewBox="0 0 28 24" aria-label="Cart"><path d="M0 2h5l4 13h14l4-10H7" fill="none" stroke="#fff" stroke-width="2.5"/><path d="M7 5h20l-4 10H10z" fill="#fff"/><circle cx="11" cy="21" r="2.5" fill="#fff"/><circle cx="22" cy="21" r="2.5" fill="#fff"/></svg>
  <div class="hero-title" style="top:262px;font-size:55px;color:var(--rose)">POTTED BEAUTY,</div>
  <div class="hero-title" style="top:330px;font-size:47px;color:var(--white)">READY TO ROOT AT HOME</div>
  <div class="btn btn-rose" style="left:430px;top:420px;width:315px;height:55px;font-size:14px;gap:14px;border:2px solid rgba(255,255,255,.4)">
    <span style="width:22px;height:22px;border-radius:50%;border:2px solid #fff"></span>Browse All Collections
    <svg width="32" height="16" viewBox="0 0 32 16"><path d="M0 8h29M22 1l7 7-7 7" fill="none" stroke="#fff" stroke-width="2.5"/></svg>
  </div>
  <svg class="abs" style="left:0;top:620px" width="1200" height="42" viewBox="0 0 1200 42" preserveAspectRatio="none"><path d="M0 42V30C40 30 60 10 100 10S170 30 200 30 260 5 300 5 370 30 400 30 460 8 500 8 570 32 600 32 660 6 700 6 770 30 800 30 860 5 900 5 970 30 1000 30 1060 10 1100 10 1160 30 1200 30V42Z" fill="var(--mauve)"/></svg>
</section>

<!-- About -->
<section>
  <div class="about-frame"></div>
  <div class="photo" role="img" aria-label="Hands holding a bouquet of peach roses and baby's breath" style="left:189px;top:759px;width:426px;height:449px;border-radius:2px;background:radial-gradient(ellipse at 50% 40%,#f2b07a,#e9c9a8 45%,#8f5a45 80%,#6b4032)"></div>
  <div class="floral-art" role="img" aria-label="Corner flourish" style="left:152px;top:726px;width:52px;height:52px"></div>
  <div class="floral-art" role="img" aria-label="Corner flourish" style="left:588px;top:726px;width:52px;height:52px"></div>
  <div class="floral-art" role="img" aria-label="Corner flourish" style="left:152px;top:1186px;width:52px;height:52px"></div>
  <div class="floral-art" role="img" aria-label="Corner flourish" style="left:588px;top:1186px;width:52px;height:52px"></div>
  <h2 class="heading abs" style="left:682px;top:768px;font-size:40px">ABOUT US</h2>
  <div class="divider-ornament" role="img" aria-label="Floral divider" style="left:682px;top:843px"></div>
  <div class="about-text">
    <p>The Willowmere Atelier is a boutique e-commerce store specializing in roses and blooming plants, created for modern plant lovers who appreciate beauty, quality, and storytelling.</p>
    <p>We are a small, women-led business in Ontario, Canada, and our audience is primarily women who are drawn to floral aesthetics, a calming user experience, and elevated design.</p>
  </div>
  <div class="btn btn-rose" style="left:682px;top:1152px;width:138px;height:40px;font-size:13px">Read More</div>
  <div class="floral-art" role="img" aria-label="Line drawing of a tulip stem" style="left:1050px;top:920px;width:150px;height:372px"></div>
</section>

<!-- Our Flowers -->
<section class="flowers">
  <h2 class="heading abs" style="left:0;width:1200px;text-align:center;top:60px;font-size:40px">OUR FLOWERS</h2>
  <div class="divider-ornament" role="img" aria-label="Floral divider" style="left:554px;top:135px"></div>
  <svg class="abs" style="left:68px;top:355px" width="26" height="46" viewBox="0 0 26 46"><path d="M24 2 3 23l21 21" fill="none" stroke="#fff" stroke-width="3"/></svg>
  <svg class="abs" style="left:1097px;top:355px" width="26" height="46" viewBox="0 0 26 46"><path d="M2 2l21 21L2 44" fill="none" stroke="#fff" stroke-width="3"/></svg>
  <div class="product-card" style="left:150px">
    <div class="photo" role="img" aria-label="Mixed bouquet of red roses, gerberas and purple blooms" style="background:radial-gradient(circle at 50% 40%,#c9384e,#e58fb0 35%,#7b6fb5 60%,#3d3a3c)"></div>
    <div class="product-name">Rosalind Blush</div><div class="product-price">C$31.99</div><div class="btn btn-plum">Shop Now</div>
  </div>
  <div class="product-card" style="left:379px">
    <div class="photo" role="img" aria-label="Bucket of pink roses" style="background:radial-gradient(circle at 50% 45%,#f4a7a2,#ef9a96 45%,#5d8a4e 80%)"></div>
    <div class="product-name">Rosalind Blush</div><div class="product-price">C$31.99</div><div class="btn btn-plum">Shop Now</div>
  </div>
  <div class="product-card" style="left:610px">
    <div class="photo" role="img" aria-label="Hat box of pastel roses with a pink ribbon" style="background:radial-gradient(circle at 50% 35%,#d8c3c9,#efe6e6 55%,#f6d7d7)"></div>
    <div class="product-name">Rosalind Blush</div><div class="product-price">C$31.99</div><div class="btn btn-plum">Shop Now</div>
  </div>
  <div class="product-card" style="left:842px">
    <div class="photo" role="img" aria-label="Vase of peonies, roses and yellow blossoms" style="background:radial-gradient(circle at 50% 40%,#f1a0b5,#e9c64a 45%,#6e6a66 80%)"></div>
    <div class="product-name">Rosalind Blush</div><div class="product-price">C$31.99</div><div class="btn btn-plum">Shop Now</div>
  </div>
  <div class="floral-art" role="img" aria-label="Line drawing of a tulip stem" style="left:0;top:430px;width:140px;height:199px;background:radial-gradient(ellipse,rgba(138,107,126,.35),transparent 70%)"></div>
</section>

<!-- Shop by Occasion -->
<section>
  <h2 class="heading abs" style="left:0;width:1200px;text-align:center;top:1973px;font-size:40px">SHOP BY OCCASION</h2>
  <div class="divider-ornament" role="img" aria-label="Floral divider" style="left:554px;top:2048px"></div>
  <div class="photo" role="img" aria-label="Birthday posy of peach and red roses with greenery" style="left:152px;top:2115px;width:287px;height:308px;background:radial-gradient(circle at 50% 35%,#f59e6e,#c8263c 40%,#7fa659 70%,#f2f2f0)"></div>
  <div class="photo" role="img" aria-label="Bouquet of peach roses and eucalyptus on linen" style="left:459px;top:2115px;width:287px;height:308px;background:radial-gradient(circle at 50% 40%,#e9b79f,#9fae94 50%,#a2907e)"></div>
  <div class="photo" role="img" aria-label="Heart arrangement of red and pink roses" style="left:765px;top:2115px;width:287px;height:308px;background:radial-gradient(circle at 50% 45%,#e79aab,#b01e36 50%,#eeeeec 75%)"></div>
  <div class="occasion-label" style="left:152px">BIRTHDAYS</div>
  <div class="occasion-label" style="left:459px">GIFTS FOR MEN</div>
  <div class="occasion-label" style="left:765px">ANNIVERSARY</div>
  <div class="floral-art" role="img" aria-label="Line drawing of a tulip stem" style="left:1070px;top:2170px;width:130px;height:372px"></div>
</section>

<!-- Latest Blog -->
<section class="blog">
  <h2 class="heading abs" style="left:0;width:1200px;text-align:center;top:52px;font-size:40px">LATEST BLOG</h2>
  <div class="divider-ornament" role="img" aria-label="Floral divider" style="left:554px;top:127px"></div>
  <article class="blog-card" style="left:150px">
    <div class="photo" role="img" aria-label="Market stall of pink and red roses" style="background:radial-gradient(circle at 45% 45%,#e0507a,#c8263c 45%,#6e5a2c 85%)"></div>
    <h3 class="blog-title">Lorem Ipsum is simply dum my text of the printing</h3>
    <p class="blog-excerpt">Lorem ipsum dolor sit amet, consectetur adipiscing elit, sed do eiusmod tempor incididunt ut labore et dolore.</p>
    <div class="btn btn-plum">Read More</div>
  </article>
  <article class="blog-card" style="left:460px">
    <div class="photo" role="img" aria-label="Pastel bouquet of roses and blue blooms" style="background:radial-gradient(circle at 50% 45%,#f0a4a2,#5e72a8 50%,#2e5a66 85%)"></div>
    <h3 class="blog-title">Lorem Ipsum is simply dum my text of the printing</h3>
    <p class="blog-excerpt">Lorem ipsum dolor sit amet, consectetur adipiscing elit, sed do eiusmod tempor incididunt ut labore et dolore.</p>
    <div class="btn btn-plum">Read More</div>
  </article>
  <article class="blog-card" style="left:784px">
    <div class="photo" role="img" aria-label="Hands holding peach roses and baby's breath" style="background:radial-gradient(circle at 50% 40%,#f2b07a,#e9d3bd 45%,#8f5a45 85%)"></div>
    <h3 class="blog-title">Lorem Ipsum is simply dum my text of the printing</h3>
    <p class="blog-excerpt">Lorem ipsum dolor sit amet, consectetur adipiscing elit, sed do eiusmod tempor incididunt ut labore et dolore.</p>
    <div class="btn btn-plum">Read More</div>
  </article>
  <div class="floral-art" role="img" aria-label="Line drawing of a tulip stem" style="left:0;top:430px;width:140px;height:220px;background:radial-gradient(ellipse,rgba(138,107,126,.35),transparent 70%)"></div>
  <svg class="abs" style="left:0;top:614px" width="1200" height="44" viewBox="0 0 1200 44" preserveAspectRatio="none"><path d="M0 44V20C40 20 70 0 110 0S190 28 230 28 300 0 340 0 420 28 460 28 530 0 570 0 650 28 690 28 760 0 800 0 880 28 920 28 990 0 1030 0 1110 28 1150 28 1190 12 1200 12V44Z" fill="var(--mauve)"/></svg>
</section>

<!-- Footer -->
<footer>
  <div class="logo" style="left:155px;top:3265px;font-size:25px"><span class="dot"></span>The Willowmere Atelier</div>
  <div class="abs" style="left:190px;width:200px;text-align:center;top:3325px;font-family:'Poppins',sans-serif;font-weight:600;font-size:15px">Follow us</div>
  <div class="social abs" style="left:198px;top:3367px" aria-label="Social links"><span></span><span></span><span></span><span></span><span></span></div>
  <div class="footer-col abs" style="left:484px;top:3262px"><h4>Shop</h4><ul><li>Shop All</li><li>Plants</li><li>Pots</li><li>Sale</li><li>Gift Card</li><li>Subscriptions</li><li>Care</li></ul></div>
  <div class="footer-col abs" style="left:625px;top:3262px"><h4>Helpful Links</h4><ul><li>FAQ</li><li>Shipping &amp; Returns</li><li>Terms &amp; Conditions</li><li>Payment Methods</li></ul></div>
  <div class="footer-col abs" style="left:836px;top:3262px">
    <h4>Contact Us</h4>
    <div class="contact-row"><svg width="12" height="16" viewBox="0 0 12 16"><path d="M6 0a6 6 0 0 1 6 6c0 4-6 10-6 10S0 10 0 6a6 6 0 0 1 6-6z" fill="#fff"/><circle cx="6" cy="6" r="2.2" fill="var(--mauve)"/></svg>PO Box 4417, Larkfield ON, K0A 2B0</div>
    <div class="contact-row"><svg width="14" height="14" viewBox="0 0 14 14"><path d="M3 0l3 3-2 2c1 2 3 4 5 5l2-2 3 3-2 3C6 14 0 8 0 2z" fill="#fff"/></svg>+1 555 014 2297</div>
    <div class="contact-row"><svg width="14" height="11" viewBox="0 0 14 11"><rect width="14" height="11" rx="1.5" fill="#fff"/><path d="M1 1l6 5 6-5" fill="none" stroke="var(--mauve)" stroke-width="1.4"/></svg>hello@willowmere.example</div>
  </div>
  <div class="abs" style="left:150px;top:3452px;width:903px;height:2px;background:rgba(255,255,255,.5)"></div>
  <div class="abs" style="left:0;width:1200px;text-align:center;top:3498px;font-size:12px">Copyright © 2025 All Rights Reserved</div>
</footer>

</body>
</html>
```